Business Card Design For Office Furniture Clearance Company

Kestrel Office Clearance - our company name pretty much explains what we do, we clear offices for high end clients, mainly plc's and large international companies.

We require a nice looking business card that displays professionalism but without being too serious.

It would be nice to see just a little more than a conventional boring business card, make sure you add some flare.

Industry/Entity Type

Office Furniture

Contact Information for Business Card

CARD 1

Mark Holloway
Director
mark@kestrelofficeclearance.co.uk
m: 07700 153928

t: 01632 960418
www.kestrelofficeclearance.co.uk

Kestrel Office Clearance
Unit K4 B
2-8 Fenwick Lane
Harwick
Stanmoor Vale
ZZ9 4QT

free office clearances… you cant get better than that.

CARD 2

Peter Radford
Director
peter@kestrelofficeclearance.co.uk
m: 07700 382615

t: 01632 960418

Kestrel Office Clearance
Unit K4 B
2-8 Fenwick Lane
Harwick
Stanmoor Vale
ZZ9 4QT

Font styles to use
Sans Serif

Requirements
Must have
• A white background - as we have a blue logo.
Nice to have
• Nice use of the logo - play around with this and dissect it.

```html
<!DOCTYPE html>
<html lang="en">
<head>
<meta charset="utf-8">
<title>Kestrel Office Clearance – Business Cards</title>
<link rel="stylesheet" href="https://fonts.googleapis.com/css2?family=Montserrat:wght@400;500;700&display=swap">
<style>
  :root {
    --brand-blue: #1a7bbf;
    --brand-navy: #1d5f95;
    --brand-pale: #e8f0f8;
    --ink: #222831;
    --card-white: #ffffff;
    --backdrop: #2a2a2c;
    --flame-warm: #f7c97a;
    --flame-soft: #fbe6c2;
  }
  * { box-sizing: border-box; margin: 0; padding: 0; }
  html, body { width: 1200px; height: 900px; overflow: hidden; }
  body {
    background: var(--backdrop);
    font-family: "Montserrat", sans-serif;
    color: var(--ink);
    position: relative;
  }
  .card {
    position: absolute;
    width: 580px;
    height: 332px;
    background: var(--card-white);
    border-radius: 22px;
    overflow: hidden;
    box-shadow: 0 18px 40px rgba(0,0,0,.45);
  }

  /* Front */
  .card--front { left: 70px; top: 90px; }
  .front__flare {
    position: absolute;
    right: 14px; top: 8px;
    width: 150px; height: 190px;
    border-radius: 60% 40% 70% 30% / 50% 60% 40% 50%;
    background: radial-gradient(ellipse at 55% 45%, var(--flame-warm) 0%, var(--flame-soft) 55%, rgba(255,255,255,0) 80%);
    opacity: .85;
  }
  .front__brand {
    position: absolute;
    left: 0; right: 0; top: 48px;
    display: flex; flex-direction: column; align-items: center; gap: 14px;
  }
  .front__disc {
    width: 160px; height: 160px; border-radius: 50%;
    background: var(--brand-blue);
  }
  .front__name {
    font-weight: 700; font-size: 19px; color: var(--brand-blue);
    letter-spacing: .5px; white-space: nowrap;
  }
  .front__tagline {
    position: absolute;
    left: 34px; bottom: 28px;
    font-size: 13px; font-weight: 500; letter-spacing: 1px;
    text-transform: uppercase; color: var(--ink);
    white-space: nowrap;
  }

  /* Back */
  .card--back { left: 560px; top: 480px; }
  .back__band {
    position: absolute; left: 0; top: 0; bottom: 0; width: 92px;
    background: var(--brand-navy);
  }
  .back__seal {
    position: absolute; left: 40px; top: 26px;
    width: 100px; height: 100px; border-radius: 50%;
    background: var(--brand-blue);
    border: 4px solid var(--card-white);
  }
  .back__ghost {
    position: absolute; right: -60px; top: 10px;
    width: 280px; height: 280px; border-radius: 50%;
    background: var(--brand-pale);
  }
  .back__content {
    position: absolute; left: 160px; top: 26px; right: 24px;
  }
  .back__company {
    font-weight: 700; font-size: 22px; color: var(--brand-navy);
    letter-spacing: .3px; text-transform: uppercase; white-space: nowrap;
  }
  .back__person {
    font-weight: 700; font-size: 19px; color: var(--brand-blue);
    text-transform: uppercase; margin-top: 4px;
  }
  .back__role {
    font-size: 13px; text-transform: uppercase; letter-spacing: .5px; margin-bottom: 6px;
  }
  .back__address { font-style: normal; font-size: 13.5px; line-height: 1.3; }
  .back__contacts { list-style: none; margin-top: 6px; font-size: 13.5px; line-height: 1.45; }
  .back__contacts li { display: flex; align-items: center; gap: 8px; }
  .back__contacts svg { width: 12px; height: 12px; fill: var(--brand-blue); flex: none; }
</style>
</head>
<body>

<section class="card card--front" aria-label="Card front">
  <div class="front__flare" role="img" aria-label="Warm flame illustration"></div>
  <div class="front__brand">
    <div class="front__disc"></div>
    <div class="front__name">Kestrel Office Clearance</div>
  </div>
  <p class="front__tagline">Free office clearances… it really is that simple</p>
</section>

<section class="card card--back" aria-label="Card back">
  <div class="back__ghost"></div>
  <div class="back__band"></div>
  <div class="back__seal"></div>
  <div class="back__content">
    <h1 class="back__company">Kestrel Office Clearance</h1>
    <h2 class="back__person">Mark Holloway</h2>
    <p class="back__role">Director</p>
    <address class="back__address">
      Kestrel Office Clearance<br>
      Unit K4 B<br>
      2-8 Fenwick Lane<br>
      Harwick<br>
      Stanmoor Vale<br>
      ZZ9 4QT
    </address>
    <ul class="back__contacts">
      <li><svg viewBox="0 0 12 12"><rect x="3" y="0" width="6" height="12" rx="1.2"/></svg>07700 153928</li>
      <li><svg viewBox="0 0 12 12"><path d="M2 1l2.5-.5 1.5 3-1.5 1a7 7 0 0 0 3 3l1-1.5 3 1.5L11 10c-5 1-10-4-9-9z"/></svg>01632 960418</li>
      <li><svg viewBox="0 0 12 12"><path d="M0 2h12v8H0z M0 2l6 4 6-4" stroke="#fff" stroke-width="1"/></svg>mark@kestrelofficeclearance.co.uk</li>
      <li><svg viewBox="0 0 12 12"><circle cx="6" cy="6" r="5.5"/><path d="M0.5 6h11M6 .5v11" stroke="#fff" stroke-width=".9"/></svg>www.kestrelofficeclearance.co.uk</li>
    </ul>
  </div>
</section>

</body>
</html>
```